Construction material supplies company business card ****

1. Full company name “K T Masonry Works Ltd”
I am after a Business card design for the company as a whole. We are better known in Solomon Islands as “K T Masonry” for short.

We are a building materials supplier of
Ready Mixed Concrete, Bricks and Blocks,
Quarry products- gravel, aggregates, sand etc.
Cement distributor/retailer of reputable brands.
Other prefab concrete products. Culverts, wave breakers, concrete retaining blocks etc.

2. Competitive Advantage over Competition: Quality, efficient, professional, dependable, reliable

3. We want people to feel trust worthy, high quality, strong when they see our brand

5. No preference to color. Maybe more sturdy and corporate. Not fancy.

Industry/Entity Type

CONSTRUCTION SUPPLY

Contact Information for Business Card

Name, Position, office phone mob phone, email

Requirements
Must have
• the company logo
Nice to have
• would like to see a mixture of designs, of with logo only and also with simple graphic designs to bring out the company whilst still have the strong sturdy professional feeling

```html
<!DOCTYPE html>
<html lang="en">
<head>
<meta charset="utf-8">
<title>K T Masonry — Business Card</title>
<link rel="stylesheet" href="https://fonts.googleapis.com/css2?family=Lato:wght@400;700;900&display=swap">
<style>
  :root {
    --backdrop: #3a3a3c;
    --card-blue: #174a76;
    --card-blue-deep: #12395d;
    --ink-white: #ffffff;
    --ink-soft: #dfe7ef;
    --silver: #d5dae0;
    --divider: rgba(255,255,255,0.75);
  }
  * { box-sizing: border-box; margin: 0; padding: 0; }
  html, body {
    width: 1200px; height: 900px; overflow: hidden;
    background: var(--backdrop);
    font-family: "Lato", sans-serif;
  }
  .canvas {
    width: 1200px; height: 900px;
    display: flex; align-items: center; justify-content: center; gap: 40px;
  }
  .card {
    width: 520px; height: 297px;
    background: linear-gradient(135deg, var(--card-blue) 0%, var(--card-blue-deep) 100%);
    border-radius: 2px;
    position: relative;
    color: var(--ink-white);
  }
  /* contact side */
  .card--contact {
    display: flex; align-items: center;
    padding: 0 36px 0 40px;
  }
  .brand-block {
    display: flex; align-items: center; gap: 10px;
    width: 230px;
  }
  .brand-mark {
    width: 16px; height: 16px; border: 2px solid var(--ink-white);
    flex: none;
  }
  .brand-name {
    font-weight: 900; font-size: 28px; letter-spacing: 1px;
    text-transform: uppercase; white-space: nowrap;
  }
  .rule {
    width: 1px; height: 120px; background: var(--divider);
    margin: 0 22px 0 14px; flex: none;
  }
  .person-name {
    font-weight: 700; font-size: 19px; letter-spacing: 0.5px;
    text-transform: uppercase;
  }
  .person-role {
    font-size: 14px; color: var(--ink-soft); margin: 2px 0 12px;
  }
  .contact-list { list-style: none; }
  .contact-list li {
    display: flex; align-items: center; gap: 6px;
    font-size: 14px; line-height: 21px; color: var(--ink-soft);
  }
  .contact-list svg { width: 11px; height: 11px; flex: none; }
  /* logo side */
  .card--brand {
    display: flex; align-items: center; justify-content: center; gap: 14px;
  }
  .card--brand .brand-mark {
    width: 24px; height: 24px; border: 3px solid var(--silver);
  }
  .card--brand .brand-name {
    font-size: 44px; color: var(--silver); letter-spacing: 2px;
  }
</style>
</head>
<body>
<main class="canvas">
  <section class="card card--contact" aria-label="Business card, contact side">
    <div class="brand-block">
      <span class="brand-mark"></span>
      <span class="brand-name">K T Masonry</span>
    </div>
    <span class="rule"></span>
    <div class="contact-block">
      <p class="person-name">Daniel Harper</p>
      <p class="person-role">President</p>
      <ul class="contact-list">
        <li>
          <svg viewBox="0 0 12 12" aria-hidden="true"><path d="M2.5 1 L4.5 1 L5.2 3.4 L4 4.4 Q5 6.8 7.6 8 L8.6 6.8 L11 7.5 L11 9.5 Q10.5 11 9 11 Q1 10 1 3 Q1 1.5 2.5 1 Z" fill="currentColor"/></svg>
          677-742-3190
        </li>
        <li>
          <svg viewBox="0 0 12 12" aria-hidden="true"><rect x="1" y="2.5" width="10" height="7" fill="none" stroke="currentColor" stroke-width="1.2"/><path d="M1 3 L6 7 L11 3" fill="none" stroke="currentColor" stroke-width="1.2"/></svg>
          info@ktmasonry.com
        </li>
        <li>
          <svg viewBox="0 0 12 12" aria-hidden="true"><circle cx="6" cy="6" r="5" fill="none" stroke="currentColor" stroke-width="1.1"/><ellipse cx="6" cy="6" rx="2.2" ry="5" fill="none" stroke="currentColor" stroke-width="1"/><path d="M1 6 H11" stroke="currentColor" stroke-width="1"/></svg>
          www.ktmasonry.com
        </li>
      </ul>
    </div>
  </section>

  <section class="card card--brand" aria-label="Business card, logo side">
    <span class="brand-mark"></span>
    <span class="brand-name">K T Masonry</span>
  </section>
</main>
</body>
</html>
```